Business Card for a mobile physiotherapy company

I need a layout for a business card for a mobile physiotherapy company.
Slogan is "Mobile Physiotherapy - Your Road To Recovery"
Phone number is 867-555-0142
Email VardenTherapy@postnest.ca (subject to change with website)
Website www.VardenTherapy.ca
My name and credentials: Luke Varden Luke Varden, BSc(kin), MPT, CAFCI, IMS
Information maybe included: Direct Billing, Services including Physiotherapy, IMS, acupuncture
Maybe include facebook and instagram logos
One side with the logo clean and sharp
Other side with details, try not to look too busy, keep everything concise

```html
<!DOCTYPE html>
<html lang="en">
<head>
<meta charset="utf-8">
<title>Varden Therapy – Business Card</title>
<link rel="stylesheet" href="https://fonts.googleapis.com/css2?family=Cinzel:wght@700&family=Lora:ital,wght@0,400;1,400&display=swap">
<style>
  :root {
    --page: #3b3b3d;
    --card: #1d1e20;
    --card-edge: #111213;
    --emboss: #3c3d40;
    --brand-green: #2f7466;
    --name-blue: #2f6aa5;
    --text-light: #e6e6e6;
    --text-muted: #c9c9c9;
    --icon-green: #2f7a66;
    --band-start: #236a61;
    --band-end: #27528a;
    --divider: #4a4b4f;
    --dot-a: #3d7fc4;
    --dot-b: #b0408a;
  }
  * { box-sizing: border-box; margin: 0; padding: 0; }
  html, body { width: 799px; height: 1200px; overflow: hidden; }
  body {
    background: var(--page);
    font-family: "Lora", Georgia, serif;
    display: flex;
    flex-direction: column;
    align-items: center;
    justify-content: center;
    gap: 80px;
  }
  .card {
    width: 620px;
    height: 360px;
    border-radius: 22px;
    background: var(--card);
    box-shadow: 0 3px 0 var(--card-edge), 0 18px 40px rgba(0,0,0,.45);
    position: relative;
    overflow: hidden;
  }

  /* Brand name placeholder: one font, one weight, one colour */
  .brand {
    display: flex;
    align-items: center;
    gap: 12px;
    font-family: "Lora", Georgia, serif;
    font-weight: 400;
    line-height: 1;
    white-space: nowrap;
  }
  .brand__square { width: 14px; height: 14px; background: currentColor; flex: none; }

  /* Front */
  .card--front { display: flex; align-items: center; justify-content: center; }
  .card--front .brand { color: var(--emboss); font-size: 44px; }
  .card--front .brand__square { width: 18px; height: 18px; }

  /* Back */
  .card--back .brand {
    color: var(--brand-green);
    font-size: 30px;
    position: absolute;
    left: 36px;
    top: 136px;
  }
  .divider {
    position: absolute; left: 318px; top: 52px;
    width: 1px; height: 200px; background: var(--divider);
  }
  .details { position: absolute; left: 346px; top: 52px; right: 20px; }
  .details__name {
    font-family: "Cinzel", "Times New Roman", serif;
    font-weight: 700;
    color: var(--name-blue);
    font-size: 27px;
    letter-spacing: 1px;
    text-transform: uppercase;
    line-height: 1.2;
  }
  .details__creds { color: var(--text-muted); font-size: 14px; margin-top: 4px; }
  .social { display: flex; align-items: center; gap: 8px; color: var(--text-light); font-size: 15px; margin-top: 18px; }
  .social__dot { width: 22px; height: 22px; border-radius: 50%; }
  .social__dot--a { background: var(--dot-a); }
  .social__dot--b { background: var(--dot-b); }
  .contact { list-style: none; margin-top: 14px; display: flex; flex-direction: column; gap: 6px; }
  .contact__item { display: flex; align-items: center; gap: 10px; color: var(--text-light); font-size: 16px; white-space: nowrap; }
  .contact__icon { width: 14px; height: 14px; flex: none; fill: var(--icon-green); }
  .slogan-band {
    position: absolute; left: 0; right: 0; bottom: 0; height: 58px;
    background: linear-gradient(90deg, var(--band-start), var(--band-end));
    display: flex; align-items: center; justify-content: center;
    color: #ffffff; font-size: 19px; font-style: italic;
  }
</style>
</head>
<body>

  <section class="card card--front" aria-label="Card front">
    <div class="brand">
      <span class="brand__square"></span>
      <span class="brand__name">Varden Therapy</span>
    </div>
  </section>

  <section class="card card--back" aria-label="Card back">
    <div class="brand">
      <span class="brand__square"></span>
      <span class="brand__name">Varden Therapy</span>
    </div>

    <div class="divider"></div>

    <div class="details">
      <h1 class="details__name">Luke Varden</h1>
      <p class="details__creds">BSc(kin), MPT, CAFCI, IMS</p>
      <div class="social">
        <span>Follow us on:</span>
        <span class="social__dot social__dot--a"></span>
        <span class="social__dot social__dot--b"></span>
      </div>
      <ul class="contact">
        <li class="contact__item">
          <svg class="contact__icon" viewBox="0 0 24 24" aria-hidden="true"><path d="M6.6 10.8a15 15 0 0 0 6.6 6.6l2.2-2.2c.3-.3.7-.4 1-.2 1.1.4 2.3.6 3.6.6.6 0 1 .4 1 1V20c0 .6-.4 1-1 1A17 17 0 0 1 3 4c0-.6.4-1 1-1h3.5c.6 0 1 .4 1 1 0 1.3.2 2.5.6 3.6.1.3 0 .7-.2 1z"/></svg>
          <span>867-555-0142</span>
        </li>
        <li class="contact__item">
          <svg class="contact__icon" viewBox="0 0 24 24" aria-hidden="true"><path d="M2 5h20v14H2zm2 2v.5l8 5 8-5V7zm0 2.8V17h16V9.8l-8 5z"/></svg>
          <span>VardenTherapy@postnest.ca</span>
        </li>
        <li class="contact__item">
          <svg class="contact__icon" viewBox="0 0 24 24" aria-hidden="true"><path d="M12 2a10 10 0 1 0 0 20 10 10 0 0 0 0-20zm6.9 6h-3a15 15 0 0 0-1.3-3.9A8 8 0 0 1 18.9 8zM12 4c.8 1.2 1.5 2.5 1.9 4h-3.8c.4-1.5 1.1-2.8 1.9-4zM4.3 14a8 8 0 0 1 0-4h3.4a16 16 0 0 0 0 4zm.8 2h3a15 15 0 0 0 1.3 3.9A8 8 0 0 1 5.1 16zm3-8h-3a8 8 0 0 1 4.3-3.9C8.8 5.3 8.4 6.6 8.1 8zM12 20c-.8-1.2-1.5-2.5-1.9-4h3.8c-.4 1.5-1.1 2.8-1.9 4zm2.3-6H9.7a14 14 0 0 1 0-4h4.6a14 14 0 0 1 0 4zm.3 5.9c.6-1.2 1-2.5 1.3-3.9h3a8 8 0 0 1-4.3 3.9zm1.7-5.9a16 16 0 0 0 0-4h3.4a8 8 0 0 1 0 4z"/></svg>
          <span>www.VardenTherapy.ca</span>
        </li>
      </ul>
    </div>

    <div class="slogan-band">Mobile Physiotherapy – Your Road To Recovery</div>
  </section>

</body>
</html>
```